Business Card for Professional Photographer

I'm looking for an eye catching modern clean design that compliments my logo/ website fonts & colours.
I specialise in architecture, corporate & commercial photography so I'm marketing to professional clients rather than portrait / wedding clients.

I would prefer to not have a solid black design.

My logo brand guide is as follows :

Main front font. : Reislust
Main font colour : #fff
Slogan front font : Ubuntu Bold
Monogram front font : Venti Medium
Container colour : #fff

I need print ready files in pdf .png & .eps formats.

Included in the files below are some screen grabs as reference to font & colours etc.

```html
<!DOCTYPE html>
<html lang="en">
<head>
<meta charset="utf-8">
<title>Clearline Studio – Business Card</title>
<link href="https://fonts.googleapis.com/css2?family=Montserrat:wght@300;400;500;600&display=swap" rel="stylesheet">
<style>
  :root {
    --backdrop: #e4e5e7;
    --card-white: #ffffff;
    --ink: #4a4a4c;
    --ink-soft: #6b6b6e;
    --gold: #c8953f;
    --gold-light: #f4e2a6;
    --gold-deep: #b88434;
    --slate: #6a6b6e;
    --sky: #b9cde6;
    --haze: #d7dbe0;
    --pavement: #a7a8ab;
  }
  * { margin: 0; padding: 0; box-sizing: border-box; }
  html, body { width: 1200px; height: 960px; overflow: hidden; }
  body {
    background: var(--backdrop);
    font-family: "Montserrat", sans-serif;
    color: var(--ink);
    position: relative;
  }
  .card {
    position: absolute;
    left: 280px;
    width: 640px;
    height: 366px;
    border-radius: 22px;
    overflow: hidden;
    box-shadow: 0 10px 28px rgba(0,0,0,.18);
    background: var(--card-white);
  }
  .card--front { top: 70px; }
  .card--back { top: 524px; }

  /* front */
  .front-photo {
    position: absolute; inset: 0;
    background: linear-gradient(180deg, var(--sky) 0%, var(--haze) 48%, var(--pavement) 100%);
    opacity: .78;
  }
  .front-veil { position: absolute; inset: 0; background: rgba(255,255,255,.28); }
  .front-brand {
    position: absolute; left: 170px; top: 150px;
    display: flex; align-items: center; gap: 16px;
  }
  .brand-square {
    width: 46px; height: 46px; border: 3px solid var(--gold); border-radius: 6px;
  }
  .brand-text { display: flex; flex-direction: column; }
  .brand-name {
    font-weight: 300; font-size: 30px; letter-spacing: 5px;
    color: var(--ink); text-transform: uppercase; line-height: 1;
  }
  .brand-tagline {
    font-weight: 600; font-size: 9px; letter-spacing: 1.6px;
    color: var(--ink); margin-top: 6px;
  }

  /* back */
  .back-brand { position: absolute; left: 42px; top: 46px; display: flex; align-items: center; gap: 16px; }
  .back-brand .brand-square { width: 60px; height: 60px; }
  .person { position: absolute; left: 42px; top: 218px; }
  .person-name { color: var(--gold); font-weight: 600; font-size: 19px; letter-spacing: .5px; text-transform: uppercase; }
  .person-title { font-size: 15px; margin-top: 2px; }
  .person-address { font-size: 15px; margin-top: 12px; line-height: 1.3; }
  .contacts {
    position: absolute; right: 40px; top: 150px;
    list-style: none; text-align: right; font-size: 14px; line-height: 1.45;
  }
  .contacts li { display: flex; align-items: center; justify-content: flex-end; gap: 8px; }
  .contacts svg { width: 13px; height: 13px; fill: var(--gold); }
  .gold-band {
    position: absolute; left: 0; bottom: 0; width: 520px; height: 44px;
    background: linear-gradient(90deg, var(--gold-deep) 0%, var(--gold-light) 55%, var(--gold) 100%);
    display: flex; align-items: center; padding-left: 42px;
    font-size: 15px; color: var(--ink); letter-spacing: .3px;
  }
  .slate-band {
    position: absolute; right: 0; bottom: 0; width: 120px; height: 44px;
    background: var(--slate);
  }
  .band-square {
    position: absolute; right: 92px; bottom: 8px; width: 30px; height: 28px;
    border: 2px solid var(--gold); border-radius: 4px; background: var(--card-white);
  }
</style>
</head>
<body>

<section class="card card--front">
  <div class="front-photo" role="img" aria-label="Photograph of a modern white and orange building against a blue sky with an empty car park"></div>
  <div class="front-veil"></div>
  <div class="front-brand">
    <div class="brand-square"></div>
    <div class="brand-text">
      <span class="brand-name">Clearline Studio</span>
      <span class="brand-tagline">Architecture Corporate Commercial</span>
    </div>
  </div>
</section>

<section class="card card--back">
  <div class="back-brand">
    <div class="brand-square"></div>
    <div class="brand-text">
      <span class="brand-name">Clearline Studio</span>
      <span class="brand-tagline">Architecture Corporate Commercial</span>
    </div>
  </div>

  <ul class="contacts">
    <li>555-210-4837
      <svg viewBox="0 0 24 24"><path d="M6.6 10.8a15 15 0 0 0 6.6 6.6l2.2-2.2a1 1 0 0 1 1-.25 11.4 11.4 0 0 0 3.6.57 1 1 0 0 1 1 1V20a1 1 0 0 1-1 1A17 17 0 0 1 3 4a1 1 0 0 1 1-1h3.5a1 1 0 0 1 1 1c0 1.25.2 2.45.57 3.57a1 1 0 0 1-.25 1z"/></svg></li>
    <li>555-318-6902
      <svg viewBox="0 0 24 24"><path d="M7 2h10a2 2 0 0 1 2 2v16a2 2 0 0 1-2 2H7a2 2 0 0 1-2-2V4a2 2 0 0 1 2-2zm0 3v13h10V5z"/></svg></li>
    <li>555-427-1596
      <svg viewBox="0 0 24 24"><path d="M6 3h12v5H6zM4 9h16a2 2 0 0 1 2 2v6h-4v4H6v-4H2v-6a2 2 0 0 1 2-2zm4 7v3h8v-3z"/></svg></li>
    <li>hello@clearlinestudio.com
      <svg viewBox="0 0 24 24"><path d="M3 5h18a1 1 0 0 1 1 1v12a1 1 0 0 1-1 1H3a1 1 0 0 1-1-1V6a1 1 0 0 1 1-1zm9 7 8-5H4z"/></svg></li>
  </ul>

  <div class="person">
    <p class="person-name">Daniel Hart</p>
    <p class="person-title">President</p>
    <p class="person-address">412 Harbor View Road<br>Juneau, Alaska 99801</p>
  </div>

  <div class="gold-band">www.clearlinestudio.com</div>
  <div class="slate-band"></div>
  <div class="band-square"></div>
</section>

</body>
</html>
```